RTavenor Business Cards & Letterhead

I have a logo but need a design for some new business cards. We are a Design-Build Firm that specializes in the design and construction of commercial projects.
the cards need to be professional. no cartoon stuff.
i would like to have the cards in AI format so I can update the card as needed. Logo is provided.
Our Address is: 4187 Marlowe Ct. Apex, North Carolina 27614

```html
<!DOCTYPE html>
<html lang="en">
<head>
<meta charset="utf-8">
<title>RTavenor Business Card</title>
<link href="https://fonts.googleapis.com/css2?family=Open+Sans:wght@400;600;700;800&display=swap" rel="stylesheet">
<style>
  :root {
    --backdrop: #303030;
    --card-dark: #1f1f23;
    --blue: #1273b4;
    --blue-deep: #0b3d66;
    --blue-mid: #145a8c;
    --grey: #6f7176;
    --grey-light: #8a8c91;
    --white: #ffffff;
  }
  * { margin: 0; padding: 0; box-sizing: border-box; }
  html, body { width: 1200px; height: 780px; overflow: hidden; }
  body {
    background: var(--backdrop);
    font-family: "Open Sans", Arial, sans-serif;
    position: relative;
  }
  .card {
    position: absolute;
    width: 540px;
    height: 309px;
    top: 236px;
    overflow: hidden;
  }
  /* Back side */
  .card-back {
    left: 40px;
    background: radial-gradient(ellipse at 50% 50%, #1478bb 0%, var(--blue-mid) 40%, var(--blue-deep) 100%);
    display: flex;
    align-items: center;
    justify-content: center;
  }
  .back-wordmark {
    font-weight: 800;
    font-size: 62px;
    letter-spacing: 1px;
    color: #0d4570;
  }
  /* Front side */
  .card-front { left: 620px; background: var(--card-dark); }
  .front-shapes { position: absolute; inset: 0; }
  .brand {
    position: absolute;
    top: 52px;
    left: 170px;
    display: flex;
    align-items: center;
    gap: 10px;
  }
  .brand-square { width: 26px; height: 26px; background: var(--blue); }
  .brand-name {
    font-weight: 800;
    font-size: 40px;
    color: var(--grey);
    letter-spacing: 0.5px;
    line-height: 1;
  }
  .person {
    position: absolute;
    left: 36px;
    top: 160px;
    text-align: right;
    width: 250px;
  }
  .person-name {
    font-weight: 700;
    font-size: 25px;
    color: var(--blue);
    letter-spacing: 1px;
    line-height: 1.1;
  }
  .person-title {
    font-weight: 600;
    font-size: 16px;
    color: var(--white);
    letter-spacing: 0.5px;
  }
  .divider {
    position: absolute;
    left: 300px;
    top: 140px;
    width: 2px;
    height: 78px;
    background: var(--white);
  }
  .contacts {
    position: absolute;
    left: 316px;
    top: 142px;
    list-style: none;
  }
  .contacts li {
    display: flex;
    align-items: center;
    gap: 8px;
    font-size: 14.5px;
    font-weight: 600;
    color: var(--white);
    line-height: 24px;
  }
  .contacts svg { width: 13px; height: 13px; fill: var(--blue); flex: none; }
  .address {
    position: absolute;
    left: 0;
    right: 0;
    bottom: 24px;
    text-align: center;
    font-size: 17px;
    font-weight: 600;
    color: var(--white);
    letter-spacing: 0.5px;
  }
</style>
</head>
<body>

<section class="card card-back" aria-label="Card back">
  <span class="back-wordmark">RTAVENOR</span>
</section>

<section class="card card-front" aria-label="Card front">
  <svg class="front-shapes" viewBox="0 0 540 309" preserveAspectRatio="none" aria-hidden="true">
    <defs>
      <radialGradient id="band-glow" cx="0.55" cy="0.75" r="0.6">
        <stop offset="0" stop-color="#1479bd"/>
        <stop offset="1" stop-color="#0b3d66"/>
      </radialGradient>
    </defs>
    <path d="M0 252 C180 250 380 220 540 150 L540 309 L0 309 Z" fill="url(#band-glow)"/>
    <path d="M20 242 C200 236 380 210 530 138 C380 218 200 242 20 244 Z" fill="var(--grey-light)"/>
  </svg>

  <div class="brand">
    <span class="brand-square"></span>
    <span class="brand-name">RTAVENOR</span>
  </div>

  <div class="person">
    <p class="person-name">ROLAND TAVENOR</p>
    <p class="person-title">Founder/President</p>
  </div>

  <div class="divider"></div>

  <ul class="contacts">
    <li>
      <svg viewBox="0 0 24 24"><path d="M6.6 10.8a15.1 15.1 0 0 0 6.6 6.6l2.2-2.2a1 1 0 0 1 1-.25 11.4 11.4 0 0 0 3.6.57 1 1 0 0 1 1 1V20a1 1 0 0 1-1 1A17 17 0 0 1 3 4a1 1 0 0 1 1-1h3.5a1 1 0 0 1 1 1c0 1.25.2 2.45.57 3.57a1 1 0 0 1-.25 1z"/></svg>
      (919) 555-0148
    </li>
    <li>
      <svg viewBox="0 0 24 24"><circle cx="12" cy="12" r="10"/><path d="M2 12h20M12 2c3 3 3 17 0 20M12 2c-3 3-3 17 0 20" stroke="#1f1f23" stroke-width="1.5" fill="none"/></svg>
      www.rtavenor.com
    </li>
    <li>
      <svg viewBox="0 0 24 24"><path d="M2 5h20v14H2z"/><path d="M2 5l10 8 10-8" stroke="#1f1f23" stroke-width="1.5" fill="none"/></svg>
      RMT@RTavenor.com
    </li>
  </ul>

  <p class="address">4187 Marlowe Ct. Apex, North Carolina 27614</p>
</section>

</body>
</html>
```